Brindle Sky Port needs a new upscale business card design for our high end aircraft hangar complex

Brindle Sky Port (BSP) is a large, upscale jet hangar complex in the US housing expensive aircraft. We need a new business card design, using our current logo. We will be attending a industry convention and need a card design that will stand out and be remembered by aircraft owners and private pilots.

Target Market(s)

Aircraft pilots or owners looking for a new upscale hangar

Industry/Entity Type

Airport

Contact Information for Business Card

I like to use very heavy card stock, 400#, double sided. Square, no rounded edges please.

Colors
3276b5
0255a3
85abd2

Requirements
Must have
• An expensive, classy design, vivid colors.
Nice to have
• Needs to look very expensive and classy, and have some "pop". Designer must be able to download or copy my current typeface or fonts.
• One card side might be black with the "Logo and Brindle Sky Port Double line image in blue (or try gold, or glossy black), and perhaps have a grayed out "K720 jet silhouette". The other card side would have our contact info, and perhaps the "BSP Logo only". I'd like my contact info 'stacked', not in a paragraph format.
Should not have
• Should not look "too busy". Having a double-sided card will help.

```html
<!DOCTYPE html>
<html lang="en">
<head>
<meta charset="utf-8">
<title>Brindle Sky Port — Business Card</title>
<link rel="stylesheet" href="https://fonts.googleapis.com/css2?family=Exo+2:wght@400;600;700&display=swap">
<style>
  :root {
    --bg: #2a2a2c;
    --card: #0d0d0e;
    --card-edge: #1c1c1e;
    --blue: #3276b5;
    --blue-deep: #0255a3;
    --blue-light: #85abd2;
    --text: #e6e6e6;
    --muted: #9a9a9a;
    --rule: #5a5a5a;
  }
  * { margin: 0; padding: 0; box-sizing: border-box; }
  html, body { width: 1200px; height: 950px; overflow: hidden; }
  body {
    background: var(--bg);
    font-family: "Exo 2", Arial, sans-serif;
    color: var(--text);
    position: relative;
  }
  .card {
    position: absolute;
    left: 250px;
    width: 700px;
    height: 400px;
    background: var(--card);
    border: 1px solid var(--card-edge);
    overflow: hidden;
  }
  .card--contact { top: 55px; }
  .card--brand { top: 495px; }

  /* contact side */
  .brand-mark {
    position: absolute;
    left: 60px; top: 55px;
    font-size: 64px;
    font-weight: 700;
    color: var(--blue);
    letter-spacing: 2px;
    line-height: 1;
  }
  .divider {
    position: absolute;
    left: 60px; right: 60px; top: 150px;
    height: 1px;
    background: var(--rule);
  }
  .address {
    position: absolute;
    right: 60px; top: 55px;
    text-align: right;
    font-size: 15px;
    line-height: 1.7;
    letter-spacing: 0.5px;
  }
  .address .web { letter-spacing: 3px; }
  .edge-dot {
    position: absolute;
    left: -20px; top: 262px;
    width: 40px; height: 40px;
    border-radius: 50%;
    background: var(--blue-deep);
  }
  .person {
    position: absolute;
    left: 60px; top: 258px;
  }
  .person .name {
    font-size: 22px;
    font-weight: 600;
    color: var(--blue);
    line-height: 1.1;
  }
  .person .role {
    font-size: 14px;
    color: var(--text);
    margin-top: 2px;
  }
  .contact-list {
    list-style: none;
    margin-top: 10px;
    font-size: 14px;
    line-height: 1.55;
  }
  .contact-list .label {
    display: inline-block;
    width: 18px;
    color: var(--blue);
    font-weight: 600;
  }

  /* brand side */
  .hero-image {
    position: absolute;
    inset: 0;
    background: radial-gradient(ellipse at 35% 30%, #2b2b2e 0%, #161617 45%, #0b0b0c 80%);
  }
  .brand-lockup {
    position: absolute;
    right: 60px; bottom: 70px;
    text-align: left;
    color: var(--blue);
    font-weight: 700;
  }
  .brand-lockup .initials {
    display: flex;
    align-items: center;
    gap: 14px;
    font-size: 72px;
    line-height: 1;
    letter-spacing: 2px;
  }
  .brand-lockup .initials .square {
    width: 18px; height: 18px;
    background: var(--blue);
  }
  .brand-lockup .full-name {
    font-size: 30px;
    line-height: 1.1;
    margin-top: 8px;
    letter-spacing: 1px;
  }
</style>
</head>
<body>

  <section class="card card--contact" aria-label="Contact side">
    <div class="brand-mark">BSP</div>
    <div class="address">
      <div>4120 Larkspur Way</div>
      <div>Fairbanks, Alaska 99701</div>
      <div class="web">www.brindleskyport.com</div>
    </div>
    <div class="divider"></div>
    <span class="edge-dot"></span>
    <div class="person">
      <div class="name">Dana Whitlock</div>
      <div class="role">CEO/Founder</div>
      <ul class="contact-list">
        <li><span class="label">P</span>(907) 555-0148</li>
        <li><span class="label">C</span>(907) 555-0193</li>
        <li><span class="label">F</span>(907) 555-0127</li>
        <li><span class="label">E</span>dana@brindleskyport.com</li>
      </ul>
    </div>
  </section>

  <section class="card card--brand" aria-label="Brand side">
    <div class="hero-image" role="img" aria-label="Faint greyed-out photo of a K720 jet on a black background"></div>
    <div class="brand-lockup">
      <div class="initials"><span class="square"></span>BSP</div>
      <div class="full-name">Brindle Sky Port</div>
    </div>
  </section>

</body>
</html>
```